Web Developer Wordpress theme

I'm a web developer but a poor designer so i need somebody to design me a cool and professional WordPress theme. I specialize in shopping cart developments and modifications as well as hosting for these system so would like the design to show this off. I am UK based and want this to also come across in the design.
As for colors and layout i am open mined just use your imaginantion i will let know what i think of your designs.
also forgot to mention my business name is valtrique
and my exsiting site is valtrique.co.uk

```html
<!DOCTYPE html>
<html lang="en">
<head>
<meta charset="utf-8">
<title>Valtrique — Serious Web Development</title>
<link rel="stylesheet" href="https://fonts.googleapis.com/css2?family=Arimo:wght@400;700&family=Source+Sans+3:wght@400;600;700&display=swap">
<style>
:root{
  --dark:#1f1f1f;
  --dark-2:#2d2d2d;
  --blue:#1aa3dd;
  --blue-deep:#0d7fb8;
  --orange:#f39019;
  --orange-deep:#e37b06;
  --text:#333333;
  --muted:#8a8a8a;
  --line:#c9c9c9;
  --red:#d0112b;
  --white:#ffffff;
}
*{box-sizing:border-box;margin:0;padding:0}
html,body{width:828px;height:1200px;overflow:hidden;background:var(--white)}
body{position:relative;font-family:"Arimo",Arial,sans-serif;color:var(--text);font-size:10px}
a{color:inherit;text-decoration:none}

/* header */
.site-header{position:absolute;left:0;top:0;width:828px;height:104px;background:linear-gradient(#343434,#1c1c1c)}
.brand{position:absolute;left:26px;top:8px;display:flex;align-items:center;gap:8px}
.brand-dot{width:40px;height:40px;border-radius:50%;background:var(--blue)}
.brand-name{font-family:"Source Sans 3",sans-serif;font-weight:600;font-size:46px;line-height:1;color:var(--orange)}
.brand-tagline{position:absolute;left:82px;top:66px;font-size:8.5px;letter-spacing:1.5px;color:#9a9a9a;border-top:1px solid #555;padding-top:2px;width:180px;text-align:center;white-space:nowrap}
.top-links{position:absolute;right:10px;top:5px;font-size:10.5px;color:var(--blue)}
.top-links span{color:#777;margin:0 2px}
.search{position:absolute;left:646px;top:40px;width:170px;height:24px;border-radius:12px;background:#2a2a2a;border:1px solid #4a4a4a;color:#888;font-size:10.5px;padding:5px 12px}
.search svg{position:absolute;right:6px;top:3px}

/* navigation */
.main-nav{position:absolute;left:0;top:103px;width:828px;height:33px;background:linear-gradient(#2fb6ee,var(--blue-deep));border-radius:6px 6px 0 0}
.main-nav .tab-active{position:absolute;left:48px;top:0;width:108px;height:33px;background:#1c1c1c;border-radius:0 0 18px 18px}
.main-nav a{position:absolute;top:10px;transform:translateX(-50%);color:var(--white);font-weight:700;font-size:10.5px;white-space:nowrap}
.main-nav a.current{top:7px;color:var(--blue)}

/* slider */
.slider{position:absolute;left:0;top:136px;width:828px;height:274px;background:linear-gradient(#d7d7d7,#eeeeee)}
.slide{position:absolute;left:20px;top:0;width:788px;height:272px;background:linear-gradient(#f6f6f6,#e4e4e4);border:1px solid #fff;box-shadow:0 2px 4px rgba(0,0,0,.2)}
.slide-art{position:absolute;left:330px;top:14px;width:250px;height:218px;background:linear-gradient(160deg,#cfe3f2,#e9d2b8 60%,#ececec)}
.slide-title{position:absolute;right:44px;top:92px;text-align:right;font-family:"Source Sans 3",sans-serif;font-weight:700;color:var(--dark-2);line-height:.92}
.slide-title .small{display:block;font-size:28px}
.slide-title .big{display:block;font-size:44px}
.slide-caption{position:absolute;left:0;top:198px;width:328px;height:72px;background:rgba(28,28,28,.95);color:#eee;font-size:9.6px;line-height:15px;padding:12px 8px 0 15px}
.slide-caption a{color:var(--orange)}
.pager{position:absolute;left:698px;top:230px;display:flex}
.pager i{width:14px;height:14px;background:#e0e0e0;border:1px solid #bbb;margin-left:-1px}
.pager i.on{background:var(--orange);border-color:var(--orange-deep)}

/* content */
.section-title{position:absolute;font-family:"Source Sans 3",sans-serif;font-weight:600;color:var(--orange)}
.welcome-title{left:21px;top:421px;font-size:25px}
.welcome-copy{position:absolute;left:24px;top:460px;width:530px;font-size:9.6px;line-height:16.5px}
.welcome-copy p+p{margin-top:16px}
.divider{position:absolute;left:15px;width:548px;height:2px;background:var(--line)}
.divider::before{content:"";position:absolute;left:0;top:0;width:85px;height:3px;background:var(--dark-2)}
.services{position:absolute;left:0;top:610px;width:563px;height:214px;background:linear-gradient(#ffffff,#ededed)}
.services-title{left:26px;top:621px;font-size:21px}
.service-icon{position:absolute;top:655px;width:95px;height:100px;border-radius:8px}
.service-caption{position:absolute;left:27px;top:771px;width:374px;height:30px;background:#262626;border-radius:3px;color:#eee;font-size:9.6px;padding:9px 13px;white-space:nowrap;overflow:hidden}
.service-caption::before{content:"";position:absolute;left:60px;top:-8px;border:8px solid transparent;border-top:0;border-bottom-color:#262626}

.testimonial-photo{position:absolute;left:70px;top:868px;width:92px;height:107px;border-radius:45px 45px 0 0;background:linear-gradient(#4a4a4a,#1e1e1e)}
.quote{position:absolute;left:175px;top:870px;width:355px;font-size:9.6px;line-height:16px;color:#444}
.quote-mark{font-family:Georgia,serif;font-size:20px;color:#c8c8c8;line-height:0;vertical-align:-6px}
.quote-name{position:absolute;left:175px;top:931px;font-weight:700;font-size:12px;color:var(--red)}
.quote-site{position:absolute;left:175px;top:948px;font-size:10px;color:var(--muted)}
.dots{position:absolute;left:534px;top:959px;display:flex;gap:2px}
.dots i{width:6px;height:6px;background:#c4c4c4}
.dots i.on{background:#333}

/* sidebar offers */
.offer{position:absolute;left:570px;width:236px;height:170px}
.offer-body{position:absolute;left:30px;top:38px;width:204px;height:130px;background:#ececec;border:1px solid #cfcfcf;border-radius:4px;box-shadow:0 2px 3px rgba(0,0,0,.15);padding:33px 4px 0 19px;font-size:9.2px;line-height:16.5px;color:#444}
.offer-head{position:absolute;left:60px;top:19px;width:175px;height:28px;background:linear-gradient(#3b3b3b,#1e1e1e);border-radius:0 4px 4px 0;color:var(--white);font-family:"Source Sans 3",sans-serif;font-weight:600;font-size:16.5px;padding:3px 0 0 19px;white-space:nowrap}
.offer-btn{position:absolute;left:60px;top:46px;width:84px;height:19px;background:linear-gradient(var(--orange),var(--orange-deep));color:var(--white);font-size:10px;padding:3px 0 0 9px;border-radius:0 0 3px 3px;white-space:nowrap}
.offer-price{position:absolute;left:0;top:0;width:71px;height:71px;border-radius:50%;background:radial-gradient(circle at 50% 35%,#3cc3f5,var(--blue-deep));border:3px solid #0b6d9f;color:var(--white);text-align:center;font-weight:700;padding-top:12px}
.offer-price b{display:block;font-size:19px;line-height:20px}
.offer-price small{font-size:10px;font-weight:400}

/* footer */
.site-footer{position:absolute;left:0;top:975px;width:828px;height:225px;background:linear-gradient(#353535,#222 40%,#1e1e1e)}
.footer-links{position:absolute;left:0;top:996px;width:828px;text-align:center;color:#ddd;font-size:10px;white-space:nowrap}
.footer-links span{color:#888;margin:0 4px}
.footer-rule{position:absolute;left:0;top:1023px;width:828px;height:1px;background:#111;box-shadow:0 1px 0 #3a3a3a}
.widget-title{position:absolute;top:1032px;font-family:"Source Sans 3",sans-serif;font-weight:400;font-size:18px;color:var(--blue)}
.widget-list{position:absolute;top:1068px;list-style:none;color:#ddd;font-size:10px}
.widget-list li{height:25px;padding:4px 0 0 11px;position:relative;border-bottom:1px solid #3e3e3e;white-space:nowrap}
.widget-list li:last-child{border-bottom:0}
.widget-list li::before{content:"";position:absolute;left:0;top:8px;width:5px;height:5px;border-radius:50%;background:var(--orange)}
.news-input{position:absolute;left:646px;top:1062px;width:170px;height:24px;background:#2c2c2c;border:1px solid #444;border-radius:3px}
.news-btn{position:absolute;left:753px;top:1095px;width:63px;height:24px;background:linear-gradient(#6a6a6a,#444);border-radius:3px;color:#eee;font-size:10px;text-align:center;padding-top:6px}
.bottom-bar{position:absolute;left:0;top:1172px;width:828px;height:28px;background:#262626;border-top:1px solid #111}
.copyright{position:absolute;left:0;top:1180px;width:828px;text-align:center;color:#999;font-size:10px}
.social{position:absolute;left:694px;top:1177px;display:flex;gap:9px}
.social i{width:15px;height:15px;border-radius:2px;background:#3f6aa8}
</style>
</head>
<body>

<header class="site-header">
  <div class="brand"><span class="brand-dot"></span><span class="brand-name">valtrique</span></div>
  <div class="brand-tagline">serious web developement</div>
  <nav class="top-links"><a href="#">Home</a><span>|</span><a href="#">Log in</a><span>|</span><a href="#">Site map</a></nav>
  <div class="search">Search
    <svg width="16" height="16" viewBox="0 0 16 16"><circle cx="6.5" cy="6.5" r="4.5" fill="none" stroke="#ddd" stroke-width="2"/><line x1="10" y1="10" x2="14" y2="14" stroke="#ddd" stroke-width="2.5"/></svg>
  </div>
</header>

<nav class="main-nav">
  <span class="tab-active"></span>
  <a class="current" href="#" style="left:103px">Home</a>
  <a href="#" style="left:225px">Services</a>
  <a href="#" style="left:355px">Addons</a>
  <a href="#" style="left:486px">E-commerce Hosting</a>
  <a href="#" style="left:612px">Blog</a>
  <a href="#" style="left:741px">Contact</a>
</nav>

<section class="slider">
  <div class="slide">
    <div class="slide-art" role="img" aria-label="Illustration of a globe wrapped in orange and pink arrows"></div>
    <h2 class="slide-title"><span class="small">Great</span><span class="big">Support</span></h2>
    <p class="slide-caption">As with all out templates and addon we know you may need support, so we offer free support with all packages you can call us or if you perfer just email us we will get back to you the same day. <a href="#">read more</a></p>
    <div class="pager"><i class="on"></i><i></i><i></i><i></i><i></i></div>
  </div>
</section>

<h1 class="section-title welcome-title">Welcome</h1>
<div class="welcome-copy">
  <p>Valtrique, is a freelance web developer specializing in online shopping cart solution whether it is just a simple Paylinq cart or a full blown shopping management system we customize and style it to your requirements.</p>
  <p>But I must explain to you how all this mistaken idea of denouncing pleasure and praising pain was born and I will give you a complete account of the system, and expound the actual teachings of the great explorer of the truth, the master-builder of human happiness. No one rejects, dislikes, or avoids pleasure itself, because it is pleasure, but because those who do not know how to pursue pleasure rationally encounter consequences that are extremely painful.</p>
</div>

<div class="divider" style="top:608px"></div>
<section class="services"></section>
<h2 class="section-title services-title">Services</h2>
<div class="service-icon" role="img" aria-label="Icon of a hosting server tower" style="left:32px;background:linear-gradient(135deg,#7fb6dc,#c9cfd3 60%,#9aa2a8)"></div>
<div class="service-icon" role="img" aria-label="Icon of a shopping cart" style="left:240px;background:linear-gradient(135deg,#ededed,#a8a8a8)"></div>
<div class="service-icon" role="img" aria-label="Icon of drafting tools" style="left:425px;background:linear-gradient(135deg,#e0e0e0,#9a9a9a)"></div>
<p class="service-caption">Fast and Secure web hosting Servers to support your e-commerce solution</p>
<div class="divider" style="top:824px"></div>

<div class="testimonial-photo" role="img" aria-label="Photo of a smiling businesswoman in a dark jacket"></div>
<blockquote class="quote"><span class="quote-mark">“</span> It was popularised in the 1960s with the release of Linotex sheets containing Lorem Ipsum passages, and more recently with desktop publishing software like Folio PageCraft including versions of Lorem Ipsum. <span class="quote-mark">”</span></blockquote>
<div class="quote-name">Maren Holloway</div>
<div class="quote-site">Teacakeshire.com</div>
<div class="dots"><i class="on"></i><i></i><i></i><i></i></div>

<aside>
  <div class="offer" style="top:430px">
    <div class="offer-body">We create addon and modules to work with the cartwell shopping cart system. If you just want a new payment gateway or more detailed reports Just ask and we will help.</div>
    <div class="offer-head">Cartwell Addons</div>
    <a class="offer-btn" href="#">ORDER NOW</a>
    <div class="offer-price"><b>£90*</b><small>*From</small></div>
  </div>
  <div class="offer" style="top:604px">
    <div class="offer-body">We create addon and modules to work with the cartwell shopping cart system. If you just want a new payment gateway or more detailed reports Just ask and we will help.</div>
    <div class="offer-head">Cartwell Templets</div>
    <a class="offer-btn" href="#">ORDER NOW</a>
    <div class="offer-price"><b>£400*</b><small>*From</small></div>
  </div>
  <div class="offer" style="top:778px">
    <div class="offer-body">We create addon and modules to work with the cartwell shopping cart system. If you just want a new payment gateway or more detailed reports Just ask and we will help.</div>
    <div class="offer-head">Shooping Software</div>
    <a class="offer-btn" href="#">ORDER NOW</a>
    <div class="offer-price"><b>£350*</b><small>*From</small></div>
  </div>
</aside>

<footer class="site-footer"></footer>
<nav class="footer-links">Addons<span>|</span>Blog<span>|</span>Contact<span>|</span>E-commerce Hosting<span>|</span>Out of Stock Notification System<span>|</span>Services</nav>
<div class="footer-rule"></div>

<h3 class="widget-title" style="left:26px">Control</h3>
<ul class="widget-list" style="left:26px;width:138px"><li>Log in</li><li>Entries RSS</li><li>Comments RSS</li><li>Pressline.org</li></ul>

<h3 class="widget-title" style="left:233px">Recent Post</h3>
<ul class="widget-list" style="left:233px;width:138px"><li>Out of Stock Notification</li><li>At Last a HOME</li></ul>

<h3 class="widget-title" style="left:423px">Tag</h3>
<ul class="widget-list" style="left:423px;width:200px"><li>new site Valtrique Web Developement</li></ul>

<h3 class="widget-title" style="left:647px">Newsletter</h3>
<div class="news-input"></div>
<div class="news-btn">Subscribe</div>

<div class="bottom-bar"></div>
<div class="copyright">All 2012 © Copyrights.valtrique.received</div>
<div class="social"><i></i><i style="background:#2aa6d8"></i><i style="background:#e4661b"></i><i style="background:#2b78b0"></i><i style="background:#c8c8c8"></i></div>

</body>
</html>
```